Detail Shop Business card design

i need a business card design for my new detailing company called 'Brisk's Polish Works'. i want an all black and white design . simple, direct and to the point. i want the designer to choose a fitting font to match the logothe front should have logo, address, phone and email and the back side should have a slogan and text indicating that we offer services on anything including cars, trucks, motorcycles and RVs. slogan will read "we take pride in your ride"
maybe also very small on the back side the IG icon with Brisks_Polish_Works

phone 208.417.6352
address 3847 E Larkin Ave
Spokane WA 99214
email: BrisksPolish@mailvexo.com

Target Market(s)

all ages , auto enthusiasts

Industry/Entity Type

Automotive

Contact Information for Business Card

the front should have logo, address, phone and email and the back side should have a slogan and text indicating that we offer services on anything including cars, trucks, motorcycles and RVs. slogan will read "we take pride in your ride"

phone 208.417.6352
address 3847 E Larkin Ave
Spokane WA 99214

Colors
000000
ffffff

Requirements
Must have
• bold font and very simple design with good spacing
Nice to have
• anything creative from the designer indicating we service any types of vehicles
Should not have
• any colors ,

```html
<!DOCTYPE html>
<html lang="en">
<head>
<meta charset="utf-8">
<title>Brisk's Polish Works – Business Card</title>
<link rel="stylesheet" href="https://fonts.googleapis.com/css2?family=Lato:ital,wght@0,400;0,900;1,900&display=swap">
<style>
  :root {
    --ink: #000000;
    --paper: #f4f4f4;
    --stage: #5a5a5a;
    --faint-light: #e2e2e2;
    --faint-dark: #151515;
    --rule-light: #9a9a9a;
    --rule-dark: #6a6a6a;
  }
  * { box-sizing: border-box; margin: 0; padding: 0; }
  html, body { width: 1200px; height: 896px; overflow: hidden; }
  body {
    background: var(--stage);
    font-family: "Lato", sans-serif;
    display: flex;
    flex-direction: column;
    align-items: center;
    justify-content: center;
    gap: 48px;
  }
  .card {
    position: relative;
    width: 660px;
    height: 377px;
    overflow: hidden;
  }
  .card--front { background: var(--paper); color: var(--ink); }
  .card--back { background: var(--ink); color: #ffffff; }

  .vehicle-art {
    position: absolute;
    left: 0; top: 0;
    width: 470px; height: 230px;
  }
  .card--front .vehicle-art {
    background: linear-gradient(180deg, var(--faint-light) 0%, var(--paper) 100%);
  }
  .card--back .vehicle-art {
    left: auto; right: 0; top: 70px;
    background: linear-gradient(180deg, var(--faint-dark) 0%, var(--ink) 100%);
  }

  .contact {
    position: absolute;
    left: 44px; top: 190px;
    font-size: 19px;
    line-height: 1.35;
  }
  .contact__row { display: flex; align-items: center; gap: 10px; }
  .contact__row--handle { font-size: 20px; margin-bottom: 8px; }
  .contact__row svg { flex: none; }

  .rule {
    position: absolute;
    height: 1px;
  }
  .card--front .rule { background: var(--rule-light); }
  .card--back .rule { background: var(--rule-dark); }
  .rule--contact { left: 280px; top: 213px; width: 120px; }
  .rule--address { left: 330px; top: 290px; width: 290px; }

  .brand {
    position: absolute;
    left: 370px; top: 120px;
    display: flex;
    align-items: center;
    gap: 14px;
  }
  .brand__mark { width: 46px; height: 46px; border-radius: 50%; background: var(--ink); flex: none; }
  .brand__name {
    font-weight: 900;
    font-size: 26px;
    line-height: 1.05;
    text-transform: uppercase;
  }

  .address {
    position: absolute;
    right: 44px; top: 300px;
    text-align: right;
    font-size: 21px;
    line-height: 1.2;
  }

  .services {
    position: absolute;
    right: 52px; top: 72px;
    width: 360px;
    text-align: right;
    font-size: 24px;
    line-height: 1.35;
  }
  .rule--slogan { right: 52px; top: 232px; width: 330px; }
  .slogan {
    position: absolute;
    right: 52px; top: 248px;
    font-size: 25px;
    letter-spacing: 0.5px;
    text-transform: uppercase;
  }
</style>
</head>
<body>
  <section class="card card--front" aria-label="Card front">
    <div class="vehicle-art" role="img" aria-label="Faint illustration of a hot rod car"></div>

    <div class="contact">
      <div class="contact__row contact__row--handle">
        <svg width="22" height="22" viewBox="0 0 22 22" aria-hidden="true"><circle cx="11" cy="11" r="11" fill="currentColor"/></svg>
        <span>Brisks_Polish_Works</span>
      </div>
      <div class="contact__row">
        <svg width="16" height="16" viewBox="0 0 24 24" aria-hidden="true"><path fill="currentColor" d="M6.6 10.8a15.1 15.1 0 0 0 6.6 6.6l2.2-2.2a1 1 0 0 1 1-.25 11.4 11.4 0 0 0 3.6.57 1 1 0 0 1 1 1V20a1 1 0 0 1-1 1A17 17 0 0 1 3 4a1 1 0 0 1 1-1h3.5a1 1 0 0 1 1 1c0 1.25.2 2.45.57 3.57a1 1 0 0 1-.25 1z"/></svg>
        <span>208.417.6352</span>
      </div>
      <div class="contact__row">
        <svg width="16" height="14" viewBox="0 0 24 20" aria-hidden="true"><path fill="currentColor" d="M2 2h20v16H2z"/><path fill="none" stroke="#f4f4f4" stroke-width="2" d="M2 2l10 9 10-9"/></svg>
        <span>BrisksPolish@mailvexo.com</span>
      </div>
    </div>
    <div class="rule rule--contact"></div>

    <div class="brand">
      <div class="brand__mark"></div>
      <div class="brand__name">Brisk's<br>Polish Works</div>
    </div>
    <div class="rule rule--address"></div>

    <div class="address">3847 E Larkin Ave<br>Spokane WA 99214</div>
  </section>

  <section class="card card--back" aria-label="Card back">
    <div class="vehicle-art" role="img" aria-label="Faint dark illustration of a hot rod car"></div>
    <p class="services">We offer services on anything including cars, trucks, motorcycles and RVs.</p>
    <div class="rule rule--slogan"></div>
    <p class="slogan">We take pride in your ride</p>
  </section>
</body>
</html>
```